Penfield Draft Works (PDWorks.net)

We need a Wordpress-based site designed for a client who provides writing and editing services for the IT industry. We have a wireframe complete for the homepage, but need all internal pages designed (based on homepage wireframe) and the entire site coded for WP.

Internal pages include: "Our Work" (with samples & testimonials); "Capabilities" (with sections to address "strategy", "coaching", "writing" and "editing"); "About Us"; and a Contact page.

Will provide all copywriting, writing samples, testimonials, and client logos.

We completely realize/acknowledge the subject matter is visually BORING! Anything at all that can be done to make it look visually appealing would be *great*! Stock photography is fine.

Please feel free to ask any questions whatsoever. Thanks for your time!

```html
<!DOCTYPE html>
<html lang="en">
<head>
<meta charset="utf-8">
<title>Penfield Draft Works</title>
<link href="https://fonts.googleapis.com/css2?family=Poppins:wght@400;500;600;700&family=Lato:wght@400;700&display=swap" rel="stylesheet">
<style>
:root{
  --blue:#1f5fae;
  --blue-dark:#17407f;
  --navy:#1c2f6b;
  --ink:#1b1b1b;
  --muted:#7a7a7a;
  --orange:#f0703a;
  --white:#ffffff;
  --line:#d9d9d9;
}
*{margin:0;padding:0;box-sizing:border-box}
html,body{width:1200px;height:3380px;overflow:hidden;background:var(--white)}
body{font-family:"Lato",sans-serif;color:var(--ink);position:relative}
.abs{position:absolute}
.btn{position:absolute;background:var(--blue);color:var(--white);font-family:"Poppins",sans-serif;font-weight:600;font-size:15px;display:flex;align-items:center;justify-content:center;border-radius:3px}
.brand .name{font-family:"Poppins",sans-serif;font-size:26px;font-weight:500;letter-spacing:.3px;border-bottom:1.5px solid var(--ink);padding-bottom:2px;white-space:nowrap}
.brand .tag{font-family:"Poppins",sans-serif;font-size:17px;letter-spacing:22px;margin-top:4px;white-space:nowrap}
/* header */
.site-header{position:absolute;top:0;left:0;width:1200px;height:96px;background:var(--white)}
.nav a{position:absolute;top:38px;font-size:15px;color:#222;text-decoration:none}
.nav a.active{border-bottom:1.5px solid #222;padding-bottom:6px}
/* hero */
.hero{position:absolute;top:96px;left:0;width:1200px;height:558px;background:linear-gradient(110deg,#1d2430 0%,#3d4450 45%,#8a8f97 75%,#a9adb3 100%)}
.hero .shade{position:absolute;inset:0;background:linear-gradient(90deg,rgba(10,15,25,.7),rgba(10,15,25,.1) 70%)}
.hero .welcome{left:109px;top:128px;font-family:"Poppins",sans-serif;font-size:38px;color:var(--white);font-weight:400}
.hero h1{position:absolute;left:109px;top:180px;font-family:"Poppins",sans-serif;font-weight:700;font-size:50px;line-height:69px;color:var(--white)}
.hero .sub{left:109px;top:326px;font-size:17px;color:var(--white)}
.dots{left:577px;top:522px;display:flex;gap:6px;align-items:center}
.dots span{width:9px;height:9px;border-radius:50%;background:var(--white)}
.dots span.on{width:14px;height:14px;border:3px solid var(--white);background:var(--blue)}
/* clients */
.clients{position:absolute;top:654px;left:0;width:1200px;height:564px;background:radial-gradient(circle at 50% 40%,#fff 0,#f6f7f9 100%)}
.section-title{position:absolute;left:0;width:1200px;text-align:center;font-family:"Poppins",sans-serif;font-weight:600;font-size:28px}
.client-box{left:171px;top:162px;width:857px;height:317px;background:var(--white);box-shadow:0 2px 10px rgba(0,0,0,.15);border-radius:3px}
.client{position:absolute;display:flex;align-items:center;gap:8px;font-family:"Poppins",sans-serif;font-weight:600;font-size:18px;color:#2a3a6a}
.client i{width:28px;height:28px;border-radius:50%;background:var(--orange);display:block}
/* capabilities */
.caps{position:absolute;top:1218px;left:0;width:1200px;height:532px;background:linear-gradient(120deg,#1a2d66 0%,#1f3f86 55%,#17456a 85%,#1c5a52 100%)}
.caps .section-title{color:var(--white)}
.caps .lead{position:absolute;top:132px;width:1200px;text-align:center;color:var(--white);font-size:15px}
.cap{position:absolute;top:199px;width:232px;height:255px;background:var(--white);text-align:center;border-radius:2px}
.cap svg{margin-top:28px}
.cap h3{font-family:"Poppins",sans-serif;font-weight:500;font-size:22px;color:var(--blue);margin-top:14px}
.cap p{font-size:14.5px;line-height:26px;color:var(--muted);margin:14px 16px 0}
.cap.active{background:var(--blue)}
.cap.active h3,.cap.active p{color:var(--white)}
.arrow{position:absolute;top:308px;width:40px;height:40px;border-radius:50%;display:flex;align-items:center;justify-content:center}
/* work */
.work{position:absolute;top:1750px;left:0;width:1200px;height:810px}
.work .lead{position:absolute;top:134px;width:1200px;text-align:center;font-size:15px}
.card{position:absolute;top:201px;width:310px;height:429px;background:var(--white);box-shadow:0 1px 8px rgba(0,0,0,.15);border-radius:3px;overflow:hidden}
.card .photo{height:205px}
.card h3{font-family:"Poppins",sans-serif;font-weight:500;font-size:19.5px;line-height:27px;margin:20px 25px 0}
.card p{font-size:15px;line-height:26px;color:var(--muted);margin:14px 25px 0}
.card a{display:block;margin:12px 25px 0;font-family:"Poppins",sans-serif;font-weight:600;font-size:15px;color:var(--blue);text-decoration:none}
/* contact band */
.band-left{position:absolute;top:2560px;left:0;width:600px;height:404px;background:linear-gradient(135deg,#2160b8,#1b4f9c)}
.band-right{position:absolute;top:2560px;left:600px;width:600px;height:404px;background:linear-gradient(135deg,#f27a3f,#e2602b)}
.band-left h2{position:absolute;left:114px;top:100px;font-family:"Poppins",sans-serif;font-weight:500;font-size:30px;line-height:39px;color:var(--white)}
.band-right h2{position:absolute;right:112px;top:100px;text-align:right;font-family:"Poppins",sans-serif;font-weight:600;font-size:27px;line-height:41px;color:#fde3d6}
.email{position:absolute;left:101px;top:228px;width:386px;height:49px;background:var(--white);border-radius:2px;font-size:15px;padding:17px 22px;color:#333}
/* footer */
.footer{position:absolute;top:2964px;left:0;width:1200px;height:416px}
.footer h4{position:absolute;top:92px;font-family:"Poppins",sans-serif;font-weight:500;font-size:22px}
.links{position:absolute;top:145px;list-style:none;font-size:15.5px;line-height:26px;color:#222}
.contact-item{position:absolute;left:111px;display:flex;gap:16px;font-size:15.5px;line-height:26px}
.contact-item svg{flex:none;margin-top:5px}
.social{position:absolute;left:925px;top:157px;display:flex;gap:29px}
.social span{width:18px;height:18px;border:2.5px solid var(--blue);border-radius:4px;display:block}
.rule{position:absolute;left:111px;width:977px;height:1px;background:var(--line)}
.copy{position:absolute;top:370px;width:1200px;text-align:center;font-size:15.5px}
</style>
</head>
<body>

<header class="site-header">
  <div class="brand abs" style="left:111px;top:18px">
    <div class="name">PENFIELD DRAFT WORKS</div>
    <div class="tag">DRAFTWORKS</div>
  </div>
  <nav class="nav">
    <a class="active" style="left:444px">HOME</a>
    <a style="left:520px">OURWORK</a>
    <a style="left:628px">CAPABILITIES</a>
    <a style="left:762px">ABOUT US</a>
    <a style="left:868px">BLOG</a>
  </nav>
  <a class="btn" style="left:958px;top:24px;width:130px;height:48px;font-size:14px">GET IN TOUCH</a>
</header>

<section class="hero" role="img" aria-label="Stock photo of a professional reviewing charts on a tablet with a pen at a desk">
  <div class="shade"></div>
  <div class="welcome abs">WELCOME TO</div>
  <h1>PENFIELD DRAFT<br>WORKS</h1>
  <div class="sub abs">Communicate Your Expertise And Your Customer Successes</div>
  <a class="btn" style="left:109px;top:374px;width:131px;height:48px">GET STARTED</a>
  <div class="dots abs"><span></span><span class="on"></span><span></span></div>
</section>

<section class="clients">
  <h2 class="section-title" style="top:78px">A SELECTION OF PAST AND CURRENT CLIENTS</h2>
  <div class="client-box abs">
    <div class="client" style="left:78px;top:64px"><i></i>Corvale</div>
    <div class="client" style="left:252px;top:64px"><i style="background:#d23a8f"></i>Lumeno</div>
    <div class="client" style="left:420px;top:64px"><i style="background:var(--navy)"></i>Arkbridge</div>
    <div class="client" style="left:650px;top:64px"><i style="background:#7b3fb0"></i>Veltrix</div>
    <div class="client" style="left:156px;top:204px"><i style="background:#f39a1e"></i>Orbisa</div>
    <div class="client" style="left:340px;top:204px"><i style="background:#e0262b"></i>Starvane</div>
    <div class="client" style="left:560px;top:204px"><i style="background:#6bb43f"></i>Pomelia</div>
  </div>
</section>

<section class="caps">
  <h2 class="section-title" style="top:82px">OUR CAPABILITIES</h2>
  <p class="lead">Text copy that explains in concise, snappy terms the value you provide to customers.</p>

  <div class="arrow" style="left:50px;background:var(--white)"><svg width="14" height="20" viewBox="0 0 14 20"><path d="M11 2 3 10l8 8" fill="none" stroke="var(--blue)" stroke-width="2.5"/></svg></div>
  <div class="arrow" style="left:1115px;background:var(--blue)"><svg width="14" height="20" viewBox="0 0 14 20"><path d="M3 2l8 8-8 8" fill="none" stroke="#fff" stroke-width="2.5"/></svg></div>

  <div class="cap" style="left:111px">
    <svg width="70" height="70" viewBox="0 0 70 70" fill="none" stroke="var(--blue)" stroke-width="2.5"><rect x="4" y="8" width="62" height="44" rx="2"/><path d="M4 18h62M26 58h18M35 52v6"/><circle cx="35" cy="36" r="9"/><circle cx="35" cy="36" r="3"/></svg>
    <h3>Strategy</h3>
    <p>Lorem ipsum dolor sit amet, consectetur adipiscing elit, sed do eiusmod tempor</p>
  </div>
  <div class="cap active" style="left:360px">
    <svg width="70" height="70" viewBox="0 0 70 70" fill="none" stroke="#fff" stroke-width="2.5"><rect x="8" y="10" width="54" height="40" rx="2"/><path d="M2 56h66"/><circle cx="30" cy="28" r="6"/><path d="M20 46c2-8 18-8 20 0"/><rect x="38" y="4" width="18" height="12" rx="2"/></svg>
    <h3>Coaching</h3>
    <p>Lorem ipsum dolor sit amet, consectetur adipiscing elit, sed do eiusmod tempor</p>
  </div>
  <div class="cap" style="left:608px">
    <svg width="70" height="70" viewBox="0 0 70 70" fill="none" stroke="var(--blue)" stroke-width="2.5"><path d="M12 4h30l10 10v52H12z"/><path d="M20 24h24M20 32h24M20 40h18M20 48h14"/><path d="M60 28 44 52l-4 6 6-3 16-24z"/></svg>
    <h3>Writing</h3>
    <p>Lorem ipsum dolor sit amet, consectetur adipiscing elit, sed do eiusmod tempor</p>
  </div>
  <div class="cap" style="left:856px">
    <svg width="70" height="70" viewBox="0 0 70 70" fill="none" stroke="var(--blue)" stroke-width="2.5"><rect x="14" y="14" width="48" height="44"/><path d="M4 14h66M14 4v66M14 48l14-14 12 12 8-8 14 14"/><circle cx="46" cy="26" r="4"/></svg>
    <h3>Editing</h3>
    <p>Lorem ipsum dolor sit amet, consectetur adipiscing elit, sed do eiusmod tempor</p>
  </div>
</section>

<section class="work">
  <h2 class="section-title" style="top:80px">OUR WORK</h2>
  <p class="lead">Text highlighting the type of work you do</p>

  <article class="card" style="left:111px">
    <div class="photo" role="img" aria-label="Photo of an engineer holding a laptop in a server room" style="background:linear-gradient(135deg,#0f2038,#2b4a72)"></div>
    <h3>Sed ut perspiciatis unde omnis iste natus error</h3>
    <p>Lorem ipsum dolor sit amet, consectetur adipiscing elit, sed do eiusmod tempor incididunt</p>
    <a>Read More ⟶</a>
  </article>
  <article class="card" style="left:445px">
    <div class="photo" role="img" aria-label="Overhead photo of a person working at a desk with devices" style="background:linear-gradient(135deg,#1d2a33,#4a5a66)"></div>
    <h3>Sed ut perspiciatis unde omnis iste natus error</h3>
    <p>Lorem ipsum dolor sit amet, consectetur adipiscing elit, sed do eiusmod tempor incididunt</p>
    <a>Read More ⟶</a>
  </article>
  <article class="card" style="left:778px">
    <div class="photo" role="img" aria-label="Photo of two colleagues reviewing documents beside server hardware" style="background:linear-gradient(135deg,#5a6470,#b9bec4)"></div>
    <h3>Sed ut perspiciatis unde omnis iste natus error</h3>
    <p>Lorem ipsum dolor sit amet, consectetur adipiscing elit, sed do eiusmod tempor incididunt</p>
    <a>Read More ⟶</a>
  </article>

  <a class="btn" style="left:523px;top:677px;width:154px;height:48px">VIEW OUR WORK</a>
</section>

<section class="band-left" role="img" aria-label="Blue-tinted photo of a business handshake">
  <h2>Feel free to contact<br>us with any questions.<br>We're happy to help.</h2>
  <a class="btn" style="left:111px;top:277px;width:138px;height:47px;background:var(--white);color:var(--blue)">GET IN TOUCH</a>
</section>
<section class="band-right" role="img" aria-label="Orange-tinted office photo with network line pattern">
  <h2>Editorial inspiration delivered<br>straight to your inbox.</h2>
  <div class="email">Enter email</div>
</section>

<footer class="footer">
  <div class="brand abs" style="left:111px;top:88px">
    <div class="name">PENFIELD DRAFT WORKS</div>
    <div class="tag">DRAFTWORKS</div>
  </div>
  <div class="contact-item" style="top:170px"><svg width="14" height="18" viewBox="0 0 14 18"><path d="M7 0a7 7 0 0 0-7 7c0 5 7 11 7 11s7-6 7-11a7 7 0 0 0-7-7zm0 10a3 3 0 1 1 0-6 3 3 0 0 1 0 6z" fill="#111"/></svg><span>Lorem ipsum dolor sit amet,<br>consectetur adipiscing elit, sed</span></div>
  <div class="contact-item" style="top:240px"><svg width="16" height="16" viewBox="0 0 16 16"><path d="M3 1l3 3-2 2c1 2 3 4 5 5l2-2 3 3-2 3C6 15 1 10 1 3z" fill="#111"/></svg><span>(555) 014 2290</span></div>
  <div class="contact-item" style="top:284px"><svg width="16" height="13" viewBox="0 0 16 13"><rect width="16" height="13" rx="1" fill="#111"/><path d="M1 1l7 6 7-6" fill="none" stroke="#fff" stroke-width="1.4"/></svg><span>info@pdworks.net</span></div>

  <h4 style="left:462px">Quik Links</h4>
  <ul class="links" style="left:462px"><li>HOME</li><li>OURWORK</li><li>CAPABILITIES</li><li>ABOUT US</li><li>BLOG</li></ul>
  <h4 style="left:685px">Company</h4>
  <ul class="links" style="left:685px"><li>TERMS&amp;CONDTIONS</li><li>PRIVACY POLICY</li><li>ABOUT US</li><li>SUPPORT</li></ul>
  <h4 style="left:925px">Socil Links</h4>
  <div class="social"><span></span><span></span><span></span><span></span></div>

  <div class="rule" style="top:340px"></div>
  <p class="copy">©Copyrights 2021 Company Name &nbsp;| &nbsp; All Rights Reserved</p>
  <div class="rule" style="top:412px"></div>
</footer>

</body>
</html>
```